Silver Bloom Marisol's Cleaning Service Business Cards Project

A business card with all contact details with logo design on there (already have a logo) eye catching Logo and contact info on one side, full logo on the back, must target upper class residential and corporate companies, fitness companies, still keep it on the feminine side of things , must look elegant

Target Market(s)

Upper class homes and corporate companies

Industry/Entity Type

Cleaning Service

Contact Information for Business Card

Name: Marisol Quenby
Position: Director
ABN: 31647209853
Email: marisolssilvercleaning@tidymail.example
Number: 0417906354

Font styles to use
Decorative

Colors

Designer to choose colors to be used in the design.

Requirements
Must have
• Available Sydney Wide, contact info and logo on one side, full logo on the back
Nice to have
• Professional appearance
Should not have
• Cheap advert looking stuff

```html
<!DOCTYPE html>
<html lang="en">
<head>
<meta charset="utf-8">
<title>Silver Bloom – Business Cards</title>
<link rel="stylesheet" href="https://fonts.googleapis.com/css2?family=Roboto+Slab:wght@400;500&family=Open+Sans:wght@400;600&display=swap">
<style>
  :root {
    --stage: #5a5a5c;
    --card-dark: #2f3341;
    --card-light: #ffffff;
    --teal: #2ee0d6;
    --teal-deep: #1bb5ad;
    --rule: #1f9aa6;
    --ink: #2a2b33;
    --ink-soft: #3a3b44;
  }
  * { box-sizing: border-box; margin: 0; padding: 0; }
  html, body { width: 1200px; height: 1000px; overflow: hidden; }
  body {
    background: var(--stage);
    position: relative;
    font-family: "Open Sans", sans-serif;
  }
  .card {
    position: absolute;
    width: 730px;
    height: 420px;
    border-radius: 26px;
    overflow: hidden;
  }

  /* Back of card */
  .card-back {
    left: 400px;
    top: 40px;
    background: var(--card-dark);
  }
  .card-back .brand {
    position: absolute;
    left: 0; right: 0;
    top: 170px;
    text-align: center;
    font-family: "Roboto Slab", serif;
    font-weight: 500;
    color: var(--teal);
  }
  .brand-name { font-size: 46px; letter-spacing: 2px; line-height: 1.1; text-transform: uppercase; }
  .brand-tagline { font-size: 15px; letter-spacing: 5px; text-transform: uppercase; margin-top: 6px; }

  /* Front of card */
  .card-front {
    left: 70px;
    top: 520px;
    background: var(--card-light);
  }
  .card-front .brand {
    position: absolute;
    right: 40px;
    top: 120px;
    width: 340px;
    text-align: center;
    font-family: "Roboto Slab", serif;
    font-weight: 500;
    color: var(--ink);
  }
  .card-front .brand-name { font-size: 34px; }
  .card-front .brand-tagline { font-size: 12px; letter-spacing: 4px; }

  .name-tab {
    position: absolute;
    left: 0;
    top: 205px;
    width: 30px;
    height: 60px;
    background: var(--teal);
  }
  .contact {
    position: absolute;
    left: 58px;
    top: 205px;
    color: var(--ink);
  }
  .person-name {
    font-family: "Roboto Slab", serif;
    font-weight: 500;
    font-size: 24px;
    line-height: 1.15;
  }
  .person-role {
    font-family: "Roboto Slab", serif;
    font-size: 17px;
    color: var(--teal-deep);
  }
  .contact-rule {
    position: absolute;
    left: 58px;
    width: 640px;
    height: 1.5px;
    background: var(--rule);
  }
  .contact-rule.upper { top: 268px; }
  .contact-rule.lower { top: 382px; }
  .details {
    position: absolute;
    left: 58px;
    top: 282px;
    font-size: 15px;
    font-weight: 600;
    color: var(--ink-soft);
    line-height: 1.5;
  }
  .detail-row { display: flex; align-items: center; gap: 8px; }
  .detail-row svg { width: 14px; height: 14px; flex: none; }
  .email-row {
    position: absolute;
    left: 250px;
    top: 304px;
    font-size: 15px;
    font-weight: 600;
    color: var(--ink-soft);
  }
</style>
</head>
<body>

  <section class="card card-back" aria-label="Card back">
    <div class="brand">
      <div class="brand-name">Silver Bloom</div>
      <div class="brand-tagline">Marisol's Cleaning Service</div>
    </div>
  </section>

  <section class="card card-front" aria-label="Card front">
    <div class="brand">
      <div class="brand-name">Silver Bloom</div>
      <div class="brand-tagline">Marisol's Cleaning Service</div>
    </div>

    <div class="name-tab"></div>
    <div class="contact">
      <div class="person-name">Marisol Quenby</div>
      <div class="person-role">Director</div>
    </div>
    <div class="contact-rule upper"></div>

    <div class="details">
      <div>ABN: 31647209853</div>
      <div class="detail-row">
        <svg viewBox="0 0 24 24" aria-hidden="true"><path fill="#2ee0d6" d="M6.6 10.8a15.1 15.1 0 0 0 6.6 6.6l2.2-2.2c.3-.3.7-.4 1-.2 1.1.4 2.3.6 3.6.6.6 0 1 .4 1 1V20c0 .6-.4 1-1 1C10.6 21 3 13.4 3 4c0-.6.4-1 1-1h3.5c.6 0 1 .4 1 1 0 1.3.2 2.5.6 3.6.1.3 0 .7-.2 1z"/></svg>
        <span>0417906354</span>
      </div>
    </div>
    <div class="email-row detail-row">
      <svg viewBox="0 0 24 24" aria-hidden="true"><rect x="2" y="4" width="20" height="16" rx="2" fill="#2ee0d6"/><path d="M3 6l9 7 9-7" fill="none" stroke="#fff" stroke-width="2"/></svg>
      <span>marisolssilvercleaning@tidymail.example</span>
    </div>
    <div class="contact-rule lower"></div>
  </section>

</body>
</html>
```